Brand new redesign of Brightpath finance website

I need a new website design that i can advertise a great low interest rate on the front page and capture input application details that will send through to my email address.

some car finance companies will be similar to this would be listed below

tallowcredit.example.com.au
mirabelfinance.example.com.au
finance725.example.com.au
quenbyfinance.example.com.au
finance91.example.com.au

Reason: I have changed the project to a committed project. all the webpages should have the same format just different content and i want to be able to edit the front page easily to update my interest rates.

Target Market(s)

Australian Finance market targeting a younger demographic

Industry/Entity Type

Finance

Coding

Coded - Design and coding required

Number of Pages Required

5+ page

Font styles to use
Serif
Sans Serif

Colors
0255a3
ffffff
cedeed

Requirements
Must have
• application capture form
• apply now buttons
• Headline rate front page

```html
<!DOCTYPE html>
<html lang="en">
<head>
<meta charset="utf-8">
<title>Brightpath Finance</title>
<link href="https://fonts.googleapis.com/css2?family=Oswald:wght@400;500&family=Roboto:wght@400;500;700&display=swap" rel="stylesheet">
<style>
:root{
  --blue:#1f87cf;
  --blue-deep:#1a77bd;
  --blue-title:#2867ad;
  --brand:#0255a3;
  --ink:#333;
  --muted:#666;
  --grey-band:#f0f0f0;
  --footer:#1f80c8;
  --black:#111;
  --white:#fff;
  --pale:#cedeed;
}
*{box-sizing:border-box;margin:0;padding:0}
html,body{width:1200px;height:2161px;overflow:hidden}
body{position:relative;background:var(--white);font-family:'Roboto',sans-serif;color:var(--ink)}
.abs{position:absolute}

/* header */
.site-header{left:0;top:0;width:1200px;height:130px;background:var(--white)}
.brand{left:100px;top:50px;display:flex;align-items:center;gap:10px}
.brand-mark{width:28px;height:28px;background:var(--brand);border-radius:50%}
.brand-name{font-family:'Roboto',sans-serif;font-weight:700;font-size:19px;color:var(--brand);letter-spacing:.5px;text-transform:uppercase;white-space:nowrap}
.top-contact{top:30px;font-size:13px;color:#555;display:flex;align-items:center;gap:8px;white-space:nowrap}
.top-divider{left:772px;top:14px;width:1px;height:46px;background:#e3e3e3}
.social-top{left:982px;top:29px;display:flex;gap:4px}
.social-top span{width:18px;height:18px;display:block}
.nav-item{top:86px;font-size:14.5px;color:#444;letter-spacing:.5px;white-space:nowrap}
.nav-item.active{color:var(--blue)}

/* hero */
.hero{left:0;top:130px;width:1200px;height:570px;background:linear-gradient(100deg,#dfe7ef 0%,#c9d6e2 30%,#5f6f82 55%,#2e3a4c 78%,#495668 100%)}
.hero-arrow{width:34px;height:34px;border-radius:50%;background:rgba(255,255,255,.35);display:flex;align-items:center;justify-content:center}
.hero-title{left:115px;top:360px;font-family:'Oswald',sans-serif;font-weight:400;font-size:60px;color:var(--blue-title);line-height:1;white-space:nowrap}
.hero-sub{left:116px;top:424px;font-family:'Oswald',sans-serif;font-size:27px;color:#1f4d7c;white-space:nowrap}
.btn-apply{left:117px;top:476px;width:136px;height:45px;background:var(--blue);color:var(--white);font-size:18px;letter-spacing:.5px;display:flex;align-items:center;justify-content:center;border-radius:2px}
.quick-contact{left:856px;top:406px;width:245px;height:294px;background:rgba(10,16,26,.92);padding:18px 20px}
.quick-contact h3{font-family:'Roboto',sans-serif;font-weight:500;font-size:20px;color:var(--white);text-align:center;margin-bottom:14px}
.field{background:var(--white);height:32px;margin-bottom:8px;font-size:10px;color:#888;padding:8px 10px}
.field.msg{height:50px}
.btn-signup{height:34px;background:var(--blue);color:var(--white);font-size:14px;display:flex;align-items:center;justify-content:center;border-radius:3px}

/* services */
.services{left:98px;top:727px;width:1002px;height:276px;display:flex}
.service{flex:1;color:var(--white);text-align:center;padding:40px 20px 0;position:relative}
.service:nth-child(odd){background:var(--blue)}
.service:nth-child(even){background:var(--blue-deep)}
.service .icon{height:56px;display:flex;align-items:center;justify-content:center;margin-bottom:14px}
.service h4{font-weight:400;font-size:16px;line-height:22px;letter-spacing:.3px;min-height:46px;display:flex;align-items:center;justify-content:center}
.service p{font-size:12px;line-height:17px;margin-top:4px}
.btn-more{position:absolute;left:50%;bottom:28px;transform:translateX(-50%);width:106px;height:30px;background:linear-gradient(#f6f6f6,#d9d9d9);color:#444;font-size:10px;display:flex;align-items:center;justify-content:center;border-radius:3px}

/* welcome */
.welcome-title{left:0;top:1044px;width:1200px;text-align:center;font-size:26px;font-weight:500;color:#333}
.welcome-title span{color:var(--blue);margin-left:8px}
.welcome-text{left:104px;top:1088px;width:992px;text-align:center;font-size:12.5px;line-height:21px;color:#666}

/* features */
.features{left:0;top:1178px;width:1200px;height:411px;background:var(--grey-band)}
.feature{top:1227px;width:310px}
.feature .photo{width:310px;height:189px}
.feature h5{font-weight:400;font-size:16px;color:#333;margin-top:20px}
.feature p{font-size:11.5px;line-height:18px;color:#666;margin-top:12px}
.feature .link{font-size:11px;color:var(--blue);margin-top:10px}

/* blog */
.blog-title{left:100px;top:1640px;font-size:21px;font-weight:500;color:#222}
.blog-title span{color:var(--blue)}
.blog-nav{left:1073px;top:1638px}
.post{top:1693px;width:490px;display:flex;gap:14px}
.post .thumb{width:210px;height:140px;border:3px solid #fff;box-shadow:0 0 0 1px #ccc,0 2px 4px rgba(0,0,0,.2);flex:none}
.post h6{font-size:12.5px;font-weight:500;color:var(--blue);margin-top:10px}
.post .date{font-size:10.5px;color:#666;margin-top:9px}
.post p{font-size:9.5px;line-height:16px;color:#666;margin-top:8px}
.post .link{font-size:11px;color:var(--blue);margin-top:8px}

/* footer */
.site-footer{left:0;top:1873px;width:1200px;height:216px;background:var(--footer)}
.fcol{top:1904px;color:var(--white)}
.fcol h6{font-size:15px;font-weight:500;letter-spacing:.5px;margin-bottom:18px;color:var(--white)}
.fcol li{list-style:none;font-size:11px;line-height:24px}
.fcol li::before{content:"›";margin-right:6px}
.fcol p{font-size:11px;line-height:19px}
.newsletter-form{display:flex;margin-top:12px}
.newsletter-form .input{width:144px;height:30px;background:var(--white);color:#888;font-size:10px;padding:9px 12px}
.newsletter-form .submit{width:54px;height:30px;background:var(--black);color:var(--white);font-size:11px;display:flex;align-items:center;justify-content:center}
.circles{display:flex;gap:16px;margin-top:16px}
.circles span{width:32px;height:32px;border:2px solid rgba(255,255,255,.85);border-radius:50%;display:block}
.copyright{left:0;top:2089px;width:1200px;height:72px;background:var(--black);color:var(--white);font-size:12px;display:flex;align-items:center;justify-content:center}
</style>
</head>
<body>

<header class="abs site-header">
  <div class="abs brand"><span class="brand-mark"></span><span class="brand-name">Brightpath Finance</span></div>
  <div class="abs top-contact" style="left:622px">
    <svg width="13" height="13" viewBox="0 0 24 24"><path fill="#1f87cf" d="M6.6 10.8a15 15 0 006.6 6.6l2.2-2.2c.3-.3.7-.4 1-.2 1.1.4 2.3.6 3.6.6.6 0 1 .4 1 1V20c0 .6-.4 1-1 1A17 17 0 013 4c0-.6.4-1 1-1h3.5c.6 0 1 .4 1 1 0 1.3.2 2.5.6 3.6.1.3 0 .7-.2 1z"/></svg>
    1.800.555.0142
  </div>
  <div class="abs top-divider"></div>
  <div class="abs top-contact" style="left:808px">
    <svg width="14" height="11" viewBox="0 0 14 11"><rect x=".7" y=".7" width="12.6" height="9.6" fill="none" stroke="#1f87cf" stroke-width="1.3"/><path d="M1 1l6 5 6-5" fill="none" stroke="#1f87cf" stroke-width="1.3"/></svg>
    info@bpf.example.com
  </div>
  <div class="abs social-top">
    <span style="background:#d8432f"></span><span style="background:#3b5998"></span><span style="background:#29a9e1"></span><span style="background:#0e76a8"></span><span style="background:#cc2b2b"></span>
  </div>
  <nav>
    <a class="abs nav-item active" style="left:393px">HOME</a>
    <a class="abs nav-item" style="left:485px">ABOUT US</a>
    <a class="abs nav-item" style="left:606px">SERVICES</a>
    <a class="abs nav-item" style="left:721px">PROJECTS</a>
    <a class="abs nav-item" style="left:845px">BLOG</a>
    <a class="abs nav-item" style="left:929px">NEWS</a>
    <a class="abs nav-item" style="left:1017px">CONTACTS</a>
  </nav>
</header>

<section class="abs hero" role="img" aria-label="Photo of two businessmen in suits reviewing documents at a bright office table"></section>
<div class="abs hero-arrow" style="left:38px;top:381px"><svg width="10" height="14" viewBox="0 0 10 14"><path d="M8 1L2 7l6 6" fill="none" stroke="#fff" stroke-width="2"/></svg></div>
<div class="abs hero-arrow" style="left:1130px;top:381px;background:rgba(0,0,0,.3)"><svg width="10" height="14" viewBox="0 0 10 14"><path d="M2 1l6 6-6 6" fill="none" stroke="#fff" stroke-width="2"/></svg></div>
<h1 class="abs hero-title">BRIGHTPATH FINANCE</h1>
<p class="abs hero-sub">Neque porro quisquam est qui dolorem</p>
<div class="abs btn-apply">APPLY NOW</div>

<form class="abs quick-contact">
  <h3>QUICK CONTACT</h3>
  <div class="field">Name</div>
  <div class="field">Email id</div>
  <div class="field">Phone</div>
  <div class="field msg">Message</div>
  <div class="btn-signup">SIGNUP</div>
</form>

<section class="abs services">
  <div class="service">
    <div class="icon"><svg width="44" height="48" viewBox="0 0 44 48"><circle cx="22" cy="13" r="11" fill="#fff"/><path d="M2 46c0-12 9-20 20-20s20 8 20 20z" fill="#fff"/></svg></div>
    <h4>BAS AGENT</h4>
    <p>Lorem Ipsum has been the industry's standard dummy text ever since the 1500s, when an unknown printer</p>
    <div class="btn-more">READ MORE</div>
  </div>
  <div class="service">
    <div class="icon"><svg width="58" height="52" viewBox="0 0 58 52"><g fill="none" stroke="#fff" stroke-width="6" stroke-dasharray="4 3.2"><circle cx="22" cy="28" r="14"/></g><circle cx="22" cy="28" r="12" fill="#fff"/><circle cx="22" cy="28" r="5" fill="#1a77bd"/><g fill="none" stroke="#fff" stroke-width="4" stroke-dasharray="3 2.5"><circle cx="46" cy="13" r="8"/><circle cx="46" cy="41" r="8"/></g><circle cx="46" cy="13" r="6" fill="#fff"/><circle cx="46" cy="13" r="2.5" fill="#1a77bd"/><circle cx="46" cy="41" r="6" fill="#fff"/><circle cx="46" cy="41" r="2.5" fill="#1a77bd"/></svg></div>
    <h4>PAYROLL AND<br>BOOKKEEPING SERVICES</h4>
    <p>Lorem Ipsum has been the industry's standard dummy text ever since the</p>
    <div class="btn-more">READ MORE</div>
  </div>
  <div class="service">
    <div class="icon"><svg width="56" height="48" viewBox="0 0 56 48"><rect x="2" y="2" width="52" height="34" rx="3" fill="none" stroke="#fff" stroke-width="4"/><rect x="22" y="36" width="12" height="6" fill="#fff"/><rect x="14" y="42" width="28" height="4" fill="#fff"/></svg></div>
    <h4>CREDIT FILE REPAIR<br>DEFAULT REMOVALS</h4>
    <p>Lorem Ipsum has been the industry's standard dummy text ever since the</p>
    <div class="btn-more">READ MORE</div>
  </div>
  <div class="service">
    <div class="icon"><svg width="50" height="48" viewBox="0 0 50 48"><path d="M36 8H8a4 4 0 00-4 4v28a4 4 0 004 4h28a4 4 0 004-4V24" fill="none" stroke="#fff" stroke-width="4"/><path d="M42 4l5 5-20 20-7 2 2-7z" fill="#fff"/></svg></div>
    <h4>DEBT CONSOLIDATION</h4>
    <p>Lorem Ipsum has been the industry's standard dummy text ever since the</p>
    <div class="btn-more">READ MORE</div>
  </div>
</section>

<h2 class="abs welcome-title">WELCOME TO<span>BRIGHTPATH FINANCE</span></h2>
<p class="abs welcome-text">Lorem ipsum dolor sit amet, consectetur adipiscing elit, sed do eiusmod tempor incididunt ut labore et dolore magna aliqua. Ut enim ad minim veniam, quis nostrud exercitation ullamco laboris nisi ut aliquip ex ea commodo consequat. Duis aute irure dolor in reprehenderit in voluptate velit esse cillum dolore eu fugiat nulla pariatur. Excepteur sint occaecat cupidatat non proident, sunt in culpa qui officia deserunt mollit anim id est laborum</p>

<section class="abs features"></section>
<article class="abs feature" style="left:101px">
  <div class="photo" role="img" aria-label="Photo of hands reviewing a printed financial bar chart" style="background:linear-gradient(135deg,#e8ecf1,#b9c8d8 60%,#5d86b8)"></div>
  <h5>NEQUE PORRO QUISQUAM</h5>
  <p>Lorem ipsum dolor sit amet, consectetur adipiscing elit. Sed blandit massa vel mauris sollicitudin dignissim. Lorem ipsum dolor sit amet, consectetur</p>
  <div class="link">READ MORE &gt;&gt;</div>
</article>
<article class="abs feature" style="left:447px">
  <div class="photo" role="img" aria-label="Photo of a smiling young woman holding a blue piggy bank" style="background:linear-gradient(135deg,#a86a3c,#d7a17a 45%,#5aa7d6)"></div>
  <h5>NEQUE PORRO QUISQUAM</h5>
  <p>Lorem ipsum dolor sit amet, consectetur adipiscing elit. Sed blandit massa vel mauris sollicitudin dignissim. Lorem ipsum dolor sit amet, consectetur</p>
  <div class="link">READ MORE &gt;&gt;</div>
</article>
<article class="abs feature" style="left:793px">
  <div class="photo" role="img" aria-label="Photo of business people discussing reports beside a laptop" style="background:linear-gradient(135deg,#c9c2b6,#eeeeee 55%,#8a8f96)"></div>
  <h5>NEQUE PORRO QUISQUAM</h5>
  <p>Lorem ipsum dolor sit amet, consectetur adipiscing elit. Sed blandit massa vel mauris sollicitudin dignissim. Lorem ipsum dolor sit amet, consectetur</p>
  <div class="link">READ MORE &gt;&gt;</div>
</article>

<h2 class="abs blog-title">LATEST <span>BLOG</span></h2>
<svg class="abs blog-nav" width="22" height="16" viewBox="0 0 22 16"><path d="M7 2L2 8l5 6M15 2l5 6-5 6" fill="none" stroke="#222" stroke-width="2"/></svg>
<article class="abs post" style="left:102px">
  <div class="thumb" role="img" aria-label="Photo of a hand with a pen over a calculator and financial charts" style="background:linear-gradient(135deg,#c4a05a,#e2e6ea 50%,#6f9bc6)"></div>
  <div>
    <h6>SIMPLY DUMMY TEXT</h6>
    <div class="date">20/08/2015</div>
    <p>Lorem Ipsum has been the industry's standard dummy text ever since the 1500s, when an unknown printer took a galley of type and scrambled it to make a type specimen book.</p>
    <div class="link">Read More &gt;&gt;</div>
  </div>
</article>
<article class="abs post" style="left:615px">
  <div class="thumb" role="img" aria-label="Photo of a business team meeting at a desk" style="background:linear-gradient(135deg,#dfe3e6,#9aa3ab 55%,#3e4650)"></div>
  <div>
    <h6>SIMPLY DUMMY TEXT</h6>
    <div class="date">20/08/2015</div>
    <p>Lorem Ipsum has been the industry's standard dummy text ever since the 1500s, when an unknown printer took a galley of type and scrambled it to make a type specimen book.</p>
    <div class="link">Read More &gt;&gt;</div>
  </div>
</article>

<footer class="abs site-footer"></footer>
<div class="abs fcol" style="left:107px">
  <h6>LINKS</h6>
  <ul><li>Customer Support</li><li>Documentation</li><li>Resources</li><li>General FAQs</li><li>Shortcodes</li></ul>
</div>
<div class="abs fcol" style="left:316px;width:218px">
  <h6>BRIGHTPATH FINANCE</h6>
  <p style="text-align:justify">Lorem Ipsum has been the industry's standard dummy text ever since the 1500s, when an unknown printer took a galley of type and scrambled it to make a type specimen book. It has survived not only five centuries, but also the leap</p>
</div>
<div class="abs fcol" style="left:604px">
  <h6>GET IN TOUCH</h6>
  <p>Address : 48 Harbour Lane,<br>Newcastle, NSW</p>
  <p style="margin-top:14px">Phone : 02 5550 1873</p>
  <p style="margin-top:14px">Email : info@bpf.example.com</p>
</div>
<div class="abs fcol" style="left:885px">
  <h6>NEWSLETTER</h6>
  <p>Your about us information would fit<br>here nicely.</p>
  <div class="newsletter-form"><div class="input">Email address</div><div class="submit">Submit</div></div>
  <div class="circles"><span></span><span></span><span></span></div>
</div>
<div class="abs copyright">Copyright © 2016. All Rights Reserved</div>

</body>
</html>
```